Professional Services - letterhead / business cards

The company (velmora partners) will provide services to Investment Funds and large investors in Spain. I have recently chosen a logo that I am attaching.

I would like a simple stationary design that i could use as letter head, business cards and "with compliments" cards.

I am not quite sure which color I will mostly use for the logo, in the email signature I will probably lean towards the white background and grey letters. I am attaching my favourite options.

Target Market(s)

Large Multinationals, Investment funds and Law firms

Industry/Entity Type

Business

Requirements
Must have
• my details are:
Luis R. Abadal
Velmora Partners S.L.
Casa de Torrelumbre
Calle de Vientoalto 27
28014 Madrid
T: +34 (91) 387-2265
M: +34 (646) 819-054
e-mail: labadal@velmorapartners.com

```html
<!DOCTYPE html>
<html lang="en">
<head>
<meta charset="utf-8">
<title>Velmora Partners – Business Cards</title>
<link rel="stylesheet" href="https://fonts.googleapis.com/css2?family=Mulish:wght@300;400&display=swap">
<style>
  :root {
    --backdrop: #ecebe8;
    --card: #58595b;
    --ink: #ffffff;
    --shadow: rgba(0, 0, 0, 0.18);
  }
  * { box-sizing: border-box; margin: 0; padding: 0; }
  html, body {
    width: 1200px;
    height: 900px;
    overflow: hidden;
    background: var(--backdrop);
    font-family: "Mulish", sans-serif;
    color: var(--ink);
  }
  .stage {
    position: relative;
    width: 1200px;
    height: 900px;
  }
  .card {
    position: absolute;
    left: 300px;
    width: 600px;
    height: 388px;
    background: var(--card);
    box-shadow: 0 6px 18px var(--shadow);
  }
  .card--front { top: 40px; }
  .card--back { top: 472px; }
  .card__frame {
    position: absolute;
    inset: 16px;
    border: 1.5px solid var(--ink);
  }
  .company-name {
    position: absolute;
    left: 0;
    right: 0;
    top: 50%;
    transform: translateY(-50%);
    text-align: center;
    font-weight: 300;
    font-size: 30px;
    letter-spacing: 0.03em;
  }
  .contact {
    position: absolute;
    left: 48px;
    top: 42px;
    font-weight: 300;
  }
  .contact__name {
    font-size: 26px;
    font-weight: 300;
    letter-spacing: 0.1em;
    text-transform: uppercase;
    line-height: 1.1;
  }
  .contact__company {
    font-size: 16px;
    letter-spacing: 0.03em;
    margin-top: 4px;
  }
  .contact__lines {
    list-style: none;
    margin-top: 36px;
    font-size: 17px;
    line-height: 1.4;
    letter-spacing: 0.03em;
  }
  .contact__label {
    display: inline-block;
    width: 26px;
  }
  .contact__address {
    font-style: normal;
    margin-top: 30px;
    font-size: 17px;
    line-height: 1.4;
    letter-spacing: 0.02em;
  }
</style>
</head>
<body>
<main class="stage">
  <section class="card card--front" aria-label="Card front">
    <div class="card__frame"></div>
    <p class="company-name">Velmora Partners</p>
  </section>

  <section class="card card--back" aria-label="Card back">
    <div class="card__frame"></div>
    <div class="contact">
      <h1 class="contact__name">Luis R. Abadal</h1>
      <p class="contact__company">Velmora Partners S.L.</p>
      <ul class="contact__lines">
        <li><span class="contact__label">T</span>+34 (91) 387-2265</li>
        <li><span class="contact__label">M</span>+34 (646) 819-054</li>
        <li><span class="contact__label">E</span>labadal@velmorapartners.com</li>
      </ul>
      <address class="contact__address">
        Casa de Torrelumbre<br>
        Calle de Vientoalto 27, 28014 Madrid
      </address>
    </div>
  </section>
</main>
</body>
</html>
```